MRT Property - Business Cards

Looking for a business card & general letterhead, signage etc design for our new logo.

Colours:
000a20
0056a2
00b5ef
0088ce
68cef2

Fonts:
Poppins
Karla

Please keep look and feel of new brand - example in the zip package I sent.

```html
<!DOCTYPE html>
<html lang="en">
<head>
<meta charset="UTF-8">
<title>MRT Property – Business Cards</title>
<link href="https://fonts.googleapis.com/css2?family=Poppins:wght@400;500;600;700&family=Karla:wght@400;500&display=swap" rel="stylesheet">
<style>
  :root {
    --navy: #000a20;
    --navy-card: #0e1429;
    --royal: #0056a2;
    --sky: #00b5ef;
    --ocean: #0088ce;
    --ice: #68cef2;
    --paper: #ffffff;
    --ink-grey: #6b6f78;
    --backdrop: #1c1d21;
  }
  * { margin: 0; padding: 0; box-sizing: border-box; }
  html, body { width: 1200px; height: 952px; overflow: hidden; }
  body {
    background: var(--backdrop);
    font-family: "Karla", sans-serif;
    position: relative;
  }
  .card {
    position: absolute;
    width: 500px;
    height: 286px;
    border-radius: 2px;
    overflow: hidden;
    box-shadow: 0 10px 30px rgba(0,0,0,.45);
  }

  /* Back of card */
  .card-back {
    left: 60px;
    top: 333px;
    background: var(--navy-card);
  }
  .card-back .accent-band {
    position: absolute;
    left: 0; top: 0;
    width: 100%; height: 12px;
    background: linear-gradient(90deg, var(--ice), var(--sky), var(--ocean));
  }
  .card-back .brand {
    position: absolute;
    left: 0; right: 0; top: 0; bottom: 0;
    display: flex;
    align-items: center;
    justify-content: center;
    gap: 14px;
  }
  .card-back .brand-dot {
    width: 22px; height: 22px;
    border-radius: 50%;
    background: var(--sky);
  }
  .card-back .brand-name {
    font-family: "Poppins", sans-serif;
    font-weight: 700;
    font-size: 40px;
    color: var(--paper);
    letter-spacing: 1px;
  }

  /* Front of card */
  .card-front {
    left: 640px;
    top: 333px;
    background: var(--paper);
  }
  .edge-bar {
    position: absolute;
    width: 10px;
    background: var(--royal);
  }
  .edge-bar.left { left: 0; top: 40px; height: 110px; }
  .edge-bar.right { right: 0; bottom: 0; height: 110px; }

  .front-brand {
    position: absolute;
    left: 40px; top: 92px;
    width: 190px;
    display: flex;
    align-items: center;
    gap: 8px;
  }
  .front-brand .brand-square {
    width: 14px; height: 14px;
    background: var(--sky);
    flex: none;
  }
  .front-brand .brand-name {
    font-family: "Poppins", sans-serif;
    font-weight: 700;
    font-size: 24px;
    color: var(--royal);
    white-space: nowrap;
  }

  .divider {
    position: absolute;
    left: 240px; top: 58px;
    width: 1px; height: 140px;
    background: #dde1e6;
  }

  .contact-block {
    position: absolute;
    left: 262px; top: 62px;
    font-family: "Poppins", sans-serif;
  }
  .person-name {
    font-size: 17px;
    font-weight: 500;
    color: var(--sky);
    letter-spacing: .3px;
    text-transform: uppercase;
  }
  .person-name .surname { color: var(--royal); font-weight: 700; }
  .person-role {
    font-size: 12px;
    color: var(--ink-grey);
    margin-top: 2px;
    margin-bottom: 16px;
  }
  .contact-list { list-style: none; }
  .contact-list li {
    display: flex;
    align-items: center;
    gap: 7px;
    font-size: 11px;
    color: var(--ink-grey);
    line-height: 20px;
  }
  .contact-list svg { width: 11px; height: 11px; flex: none; fill: var(--royal); }

  .address {
    position: absolute;
    left: 40px; bottom: 40px;
    font-family: "Poppins", sans-serif;
    font-size: 11px;
    color: var(--ink-grey);
  }
</style>
</head>
<body>

  <section class="card card-back" aria-label="Business card back">
    <div class="accent-band"></div>
    <div class="brand">
      <span class="brand-dot"></span>
      <span class="brand-name">MRT Property</span>
    </div>
  </section>

  <section class="card card-front" aria-label="Business card front">
    <div class="edge-bar left"></div>
    <div class="edge-bar right"></div>

    <div class="front-brand">
      <span class="brand-square"></span>
      <span class="brand-name">MRT Property</span>
    </div>

    <div class="divider"></div>

    <div class="contact-block">
      <p class="person-name">Daniel K. <span class="surname">Morrow</span></p>
      <p class="person-role">Managing Director</p>
      <ul class="contact-list">
        <li>
          <svg viewBox="0 0 24 24" aria-hidden="true"><path d="M6.6 10.8a15.1 15.1 0 0 0 6.6 6.6l2.2-2.2c.3-.3.7-.4 1-.2 1.1.4 2.3.6 3.6.6.6 0 1 .4 1 1V20c0 .6-.4 1-1 1A17 17 0 0 1 3 4c0-.6.4-1 1-1h3.5c.6 0 1 .4 1 1 0 1.3.2 2.5.6 3.6.1.3 0 .7-.2 1z"/></svg>
          +00 555 210 34
        </li>
        <li>
          <svg viewBox="0 0 24 24" aria-hidden="true"><path d="M2 5h20v14H2z M2 5l10 8 10-8" fill="none" stroke="#0056a2" stroke-width="2.5"/></svg>
          hello@mrtproperty.com
        </li>
        <li>
          <svg viewBox="0 0 24 24" aria-hidden="true"><circle cx="12" cy="12" r="9.5" fill="none" stroke="#0056a2" stroke-width="2.5"/><path d="M2.5 12h19M12 2.5c3 3 3 16 0 19M12 2.5c-3 3-3 16 0 19" fill="none" stroke="#0056a2" stroke-width="2"/></svg>
          www.mrtproperty.com
        </li>
      </ul>
    </div>

    <p class="address">2710 Harbor View Avenue Portland, OR 97205</p>
  </section>

</body>
</html>
```